Revamp Marketing Website For Video Production Website

need to revamp current website www.kestrelfilmstudio.net
reference sites www.vantora.net & http://layoutcrate.net/kestrel/
Use all current content on current kestrel website. I want a revamped modenr look. Sometbing that wows customers.
reference site www.vantora.net
Target Market(s)
business owners
Industry/Entity Type
Video Production
Number of Pages Required
5+ page
Colors
Designer to choose colors to be used in the design.
Requirements
Must have
- need to revamp current website www.kestrelfilmstudio.net
- reference sites www.vantora.net & http://layoutcrate.net/kestrel/
- Use all current content on current kestrel website. I want a revamped modenr look. Sometbing that wows customers.
- reference site www.vantora.net
Nice to have
Should not have

```html
<!DOCTYPE html>
<html lang="en">
<head>
<meta charset="utf-8">
<title>Kestrel — Marketing Videos Made For You</title>
<link href="https://fonts.googleapis.com/css2?family=Lato:wght@400;700;900&display=swap" rel="stylesheet">
<style>
:root{
  --blue:#1e9be9;
  --blue-dark:#1586d0;
  --navy:#0d1836;
  --ink:#1e1e1e;
  --muted:#555;
  --card:#f1f1f1;
  --band:#ededed;
  --soft:#f5f5f5;
  --footer:#2b2b2b;
  --footer-deep:#1d1d1d;
  --white:#fff;
}
*{box-sizing:border-box;margin:0;padding:0}
html,body{width:1200px;height:4986px;overflow:hidden}
body{position:relative;font-family:"Lato",Arial,sans-serif;color:var(--ink);background:var(--white)}
.abs{position:absolute}

/* header + hero */
.hero{position:absolute;left:0;top:0;width:1200px;height:860px;
  background:linear-gradient(120deg,#0a1430 0%,#1b3466 45%,#253f7a 60%,#0e1c42 100%);
  clip-path:polygon(0 0,100% 0,100% 86%,0 100%)}
.hero-shade{position:absolute;inset:0;background:radial-gradient(ellipse at 50% 40%,rgba(60,110,200,.35),transparent 70%)}
.brand{position:absolute;left:73px;top:44px;display:flex;align-items:center;gap:10px}
.brand-mark{width:26px;height:26px;background:var(--blue)}
.brand-name{font-size:38px;font-weight:900;letter-spacing:3px;color:var(--white);line-height:1}
.brand-tag{position:absolute;left:73px;top:84px;font-size:11px;font-weight:700;letter-spacing:1px;color:#cfe3ff}
.nav{position:absolute;left:376px;top:58px;display:flex;gap:22px;font-size:13px;font-weight:700;color:var(--white)}
.pill{position:absolute;top:53px;height:40px;border-radius:20px;font-size:13px;font-weight:700;color:var(--white);display:flex;align-items:center;justify-content:center}
.pill-outline{left:914px;width:100px;border:2px solid var(--white)}
.pill-fill{left:1027px;width:97px;background:var(--blue)}
.hero-title{position:absolute;left:0;width:1200px;top:268px;text-align:center;color:var(--white);font-weight:900;font-size:46px;line-height:56px;letter-spacing:.5px}
.hero-sub{position:absolute;left:0;width:1200px;top:398px;text-align:center;color:var(--white);font-weight:900;font-size:28px}
.cta{position:absolute;left:425px;top:462px;width:355px;height:50px;border-radius:25px;background:var(--blue);color:var(--white);font-weight:900;font-size:16px;display:flex;align-items:center;justify-content:center}
.hero-note{position:absolute;left:0;width:1200px;top:528px;text-align:center;color:var(--white);font-size:15px}

/* promo box */
.promo{position:absolute;left:73px;top:665px;width:1057px;height:532px;background:var(--white);box-shadow:0 6px 24px rgba(0,0,0,.12)}
.promo h2{position:absolute;left:0;width:100%;top:28px;text-align:center;font-size:32px;font-weight:900}
.promo p{position:absolute;left:150px;width:757px;top:82px;text-align:center;font-size:15px;line-height:24px;color:var(--muted)}
.promo-blue{position:absolute;left:27px;top:166px;width:1000px;height:332px;background:var(--blue);box-shadow:0 6px 18px rgba(30,155,233,.35)}
.promo-blue h3{position:absolute;left:40px;top:20px;width:520px;color:var(--white);font-size:47px;line-height:50px;font-weight:900}
.channels{position:absolute;left:598px;top:20px;display:grid;grid-template-columns:repeat(3,93px);gap:28px 30px}
.channel{width:93px;height:86px;border:3px solid var(--white);border-radius:12px;display:flex;align-items:center;justify-content:center}
.channel span{width:22px;height:22px;border-radius:50%;background:var(--white)}

/* examples */
.examples{position:absolute;left:0;top:1220px;width:1200px;height:560px;background:var(--band);clip-path:polygon(0 0,100% 9%,100% 86%,0 100%)}
.examples h2{position:absolute;left:73px;top:168px;font-size:48px;line-height:48px;font-weight:900}
.select{position:absolute;left:73px;top:282px;width:332px;height:40px;background:var(--white);border:1px solid #ccc;font-size:13px;font-weight:700;padding:0 14px;display:flex;align-items:center;justify-content:space-between}
.more{position:absolute;left:73px;top:342px;width:127px;height:38px;background:var(--blue);color:var(--white);font-size:13px;font-weight:900;display:flex;align-items:center;justify-content:center}
.thumb{position:absolute;top:180px;width:336px;height:190px}
.thumb-a{left:445px;background:linear-gradient(135deg,#1a1a1a,#5a5f6a 60%,#2d2f36)}
.thumb-b{left:791px;background:linear-gradient(135deg,#2c2c2c,#6c6a62 55%,#1f1f1f)}
.play{position:absolute;left:50%;top:50%;width:48px;height:34px;margin:-17px 0 0 -24px;border-radius:8px;background:rgba(0,0,0,.7);display:flex;align-items:center;justify-content:center}

/* features */
.section-title{position:absolute;left:0;width:1200px;text-align:center;font-size:32px;font-weight:900}
.feature-card{position:absolute;height:178px;background:var(--card);padding:30px 34px}
.feature-card h4{color:var(--blue);font-size:24px;font-weight:900;line-height:28px}
.feature-card h5{font-size:16px;font-weight:900;margin-top:6px;line-height:20px}
.feature-card p{font-size:14px;color:var(--muted);line-height:20px;margin-top:4px}
.feature-card a{display:block;color:var(--blue);font-size:13px;font-weight:700;margin-top:6px}
.right{text-align:right}
.circle{position:absolute;width:150px;height:150px;border-radius:50%;background:var(--blue);display:flex;align-items:center;justify-content:center}

/* sizes */
.sizes{position:absolute;left:0;top:3210px;width:1200px;height:1387px;background:var(--soft)}
.size-panel{position:absolute;background:var(--blue);color:var(--white);padding:34px 30px;font-size:19px;font-weight:900;line-height:28px}
.size-panel small{display:block;font-size:15px;line-height:22px;margin-top:12px;font-weight:700}
.tiles{position:absolute;display:grid;grid-template-columns:repeat(2,323px);grid-template-rows:repeat(2,180px);gap:6px}
.tile{width:323px;height:180px}

/* footer */
.footer{position:absolute;left:0;top:4597px;width:1200px;height:339px;background:var(--footer);color:var(--white)}
.footer .brand{top:100px}
.footer .brand-tag{top:141px;color:var(--white)}
.footer-claim{position:absolute;left:73px;top:192px;color:var(--blue);font-size:14px;font-weight:900}
.footer-text{position:absolute;left:73px;top:214px;width:380px;font-size:14px;line-height:20px;color:#ddd}
.footer h6{position:absolute;font-size:17px;font-weight:900;letter-spacing:.5px}
.links{position:absolute;left:525px;top:96px;list-style:none;font-size:13px;line-height:33px;color:#ddd}
.email{position:absolute;left:765px;top:96px;width:315px;height:40px;border-radius:20px;background:var(--white);color:#666;font-size:13px;padding:0 18px;display:flex;align-items:center}
.signup{position:absolute;left:957px;top:150px;width:123px;height:34px;border-radius:17px;background:var(--blue);font-size:13px;font-weight:900;display:flex;align-items:center;justify-content:center}
.follow{position:absolute;left:765px;top:258px;display:flex;gap:14px}
.follow span{width:20px;height:20px;border-radius:50%;background:var(--white)}
.bottom{position:absolute;left:0;top:4936px;width:1200px;height:50px;background:var(--footer-deep);color:#bbb;font-size:12px;display:flex;align-items:center;justify-content:center}
.bottom b{position:absolute;right:20px;color:var(--blue);font-weight:400}
</style>
</head>
<body>

<header class="hero" role="img" aria-label="Businesswoman holding a laptop in front of a wall of video screens">
  <div class="hero-shade"></div>
</header>
<div class="brand"><span class="brand-mark"></span><span class="brand-name">KESTREL</span></div>
<div class="brand-tag">MARKETING VIDEOS MADE FOR YOU</div>
<nav class="nav"><span>HOME</span><span>HOW IT WORKS</span><span>EXAMPLES</span><span>FAQ</span><span>CONTACT US</span><span>PRICING</span></nav>
<div class="pill pill-outline">LOG IN</div>
<div class="pill pill-fill">SIGN UP</div>
<h1 class="hero-title">ATTENTION GRABBING "VIRAL"<br>TYPE VIDEO ADS</h1>
<div class="hero-sub">ALL DELIVERED IN 24 HOURS!</div>
<div class="cta">GET ONE FREE VIDEO MOCKUP NOW</div>
<div class="hero-note">No Purchase Necessary</div>

<section class="examples">
  <h2>OUR<br>EXAMPLES</h2>
  <div class="select">MARKETING <span>&#8693;</span></div>
  <div class="more">MORE INFO</div>
  <div class="thumb thumb-a" role="img" aria-label="Example video: businessman celebrating boosted sales"><div class="play"><svg width="16" height="16" viewBox="0 0 16 16"><path d="M4 2l10 6-10 6z" fill="#fff"/></svg></div></div>
  <div class="thumb thumb-b" role="img" aria-label="Example video: person holding cash with bold headline"><div class="play"><svg width="16" height="16" viewBox="0 0 16 16"><path d="M4 2l10 6-10 6z" fill="#fff"/></svg></div></div>
</section>

<section class="promo">
  <h2>PROMOTE ANYTHING ANYWHERE ON THE WEB</h2>
  <p>Still using static image ads with Friendlane, Photoloop, Workwire, Blinkchat advertising platforms? Turn them into VIDEO ADS and get higher conversion rates instantly.</p>
  <div class="promo-blue">
    <h3>WE CREATE AWARD WINNING PROMOTIONAL MARKETING VIDEOS TO USE ALL OVER THE WEB</h3>
    <div class="channels">
      <div class="channel"><span></span></div><div class="channel"><span></span></div><div class="channel"><span></span></div>
      <div class="channel"><span></span></div><div class="channel"><span></span></div><div class="channel"><span></span></div>
      <div class="channel"><span></span></div><div class="channel"><span></span></div><div class="channel"><span></span></div>
    </div>
  </div>
</section>

<h2 class="section-title" style="top:1790px">OUR FEATURES</h2>

<!-- row 1 -->
<div class="circle" style="left:206px;top:1895px"><svg width="70" height="70" viewBox="0 0 70 70"><circle cx="35" cy="35" r="30" fill="none" stroke="#fff" stroke-width="3"/><path d="M20 36l10 10 20-22" fill="none" stroke="#fff" stroke-width="4"/></svg></div>
<div class="feature-card right" style="left:392px;top:1880px;width:738px">
  <h4>DONE FOR YOU</h4><h5>YOU DON'T LIFT A FINGER!</h5>
  <p>We make it super affordable and we DO IT ALL FOR YOU. You'll receive<br>a fully packaged, professional video...</p><a>Read More</a>
</div>
<!-- row 2 -->
<div class="feature-card" style="left:206px;top:2096px;width:608px">
  <h4>PREMIUM CONTENT</h4><h5>YOUR BUSINESS WILL LOOK SUPER HIGH END &amp; PROFESSIONAL</h5>
  <p>We have access to millions of premium video clips, fully packaged by Award Winning Videographers...</p><a>Read More</a>
</div>
<div class="circle" style="left:840px;top:2111px"><svg width="60" height="70" viewBox="0 0 60 70"><path d="M8 4h32l14 14v48H8z" fill="none" stroke="#fff" stroke-width="3"/><path d="M18 30h26M18 40h26M18 50h18" stroke="#fff" stroke-width="3"/></svg></div>
<!-- row 3 -->
<div class="circle" style="left:206px;top:2327px"><svg width="60" height="70" viewBox="0 0 60 70"><rect x="8" y="4" width="44" height="50" rx="3" fill="none" stroke="#fff" stroke-width="3"/><circle cx="30" cy="28" r="10" fill="none" stroke="#fff" stroke-width="3"/><path d="M22 50l-4 16 12-6 12 6-4-16" fill="none" stroke="#fff" stroke-width="3"/></svg></div>
<div class="feature-card right" style="left:392px;top:2312px;width:738px">
  <h4>FULLY LICENSED TO YOU</h4><h5>YOU OWN ALL THE VIDEOS TO USE FOREVER - CONSIDER THEM ASSETS!</h5>
  <p>The videos are your property and come with a lifetime license for unlimited<br>sharing and use...</p><a>Read More</a>
</div>
<!-- row 4 -->
<div class="feature-card" style="left:206px;top:2528px;width:608px">
  <h4>PERFECT LENGTH FOR MARKETING VIDEOS</h4><h5>STAND OUT FROM THE CROWD WITH VIDEO MARKETING</h5>
  <p>Our Marketing Videos range from 10 seconds up to 30 seconds in length. These are the recommended...</p><a>Read More</a>
</div>
<div class="circle" style="left:840px;top:2543px"><svg width="70" height="60" viewBox="0 0 70 60"><path d="M6 54h58" stroke="#fff" stroke-width="3"/><rect x="12" y="30" width="8" height="24" fill="none" stroke="#fff" stroke-width="3"/><rect x="26" y="18" width="8" height="36" fill="none" stroke="#fff" stroke-width="3"/><rect x="40" y="24" width="8" height="30" fill="none" stroke="#fff" stroke-width="3"/><rect x="54" y="8" width="8" height="46" fill="none" stroke="#fff" stroke-width="3"/></svg></div>
<!-- row 5 -->
<div class="circle" style="left:206px;top:2759px"><svg width="74" height="50" viewBox="0 0 74 50"><rect x="3" y="5" width="46" height="40" rx="6" fill="none" stroke="#fff" stroke-width="3"/><path d="M49 20l20-12v34L49 30z" fill="none" stroke="#fff" stroke-width="3"/></svg></div>
<div class="feature-card right" style="left:392px;top:2744px;width:738px">
  <h4>FRIENDLANE VIDEO COVER</h4><h5>"WOW" CUSTOMERS WITH A BEAUTIFUL DESIGNED FRIENDLANE<br>COVER VIDEO FOR YOUR BUSINESS</h5>
  <p>We can convert any video to a Friendlane Video Cover for your business page.</p><a>Read More</a>
</div>
<!-- row 6 -->
<div class="feature-card" style="left:206px;top:2960px;width:608px">
  <h4>BEST SUPPORT</h4><h5>WE ARE AVAILABLE TO YOU AT ALL TIMES FOR ANY KIND OF SUPPORT</h5>
  <p>Reach out anytime, anywhere. Our team of tech, marketing and video experts are here to help you...</p><a>Read More</a>
</div>
<div class="circle" style="left:840px;top:2975px"><svg width="70" height="60" viewBox="0 0 70 60"><path d="M6 8h40v26H22l-10 8v-8H6z" fill="none" stroke="#fff" stroke-width="3"/><path d="M50 18h14v24h-6v8l-10-8H30v-4" fill="none" stroke="#fff" stroke-width="3"/></svg></div>

<section class="sizes">
  <h2 class="section-title" style="top:56px">VIDEO SIZES AVAILABLE</h2>

  <div class="size-panel" style="left:73px;top:187px;width:392px;height:259px;clip-path:polygon(0 8%,100% 0,100% 100%,0 100%)">Wide Screen Videos – This size is a standard video size that works best for pretty much anywhere on the web (1080x720)<small>Included with all video purchases</small></div>
  <div class="tiles" style="left:472px;top:130px">
    <div class="tile" role="img" aria-label="Burger on a wooden board" style="background:linear-gradient(135deg,#3a2616,#a0662e)"></div>
    <div class="tile" role="img" aria-label="Man working outdoors at a table" style="background:linear-gradient(135deg,#6d7a52,#b49a72)"></div>
    <div class="tile" role="img" aria-label="Chef tossing food in a pan" style="background:linear-gradient(135deg,#2a2a2a,#8d7a66)"></div>
    <div class="tile" role="img" aria-label="Couple looking at a tablet" style="background:linear-gradient(135deg,#5b4634,#c7a17c)"></div>
  </div>

  <div class="tiles" style="left:73px;top:546px">
    <div class="tile" role="img" aria-label="Suburban house exterior" style="background:linear-gradient(135deg,#8fa7c4,#6f5a44)"></div>
    <div class="tile" role="img" aria-label="Glowing light bulb" style="background:linear-gradient(135deg,#1c130a,#c98a2e)"></div>
    <div class="tile" role="img" aria-label="Hand with a glass of drink" style="background:linear-gradient(135deg,#6e3b1e,#d6b48a)"></div>
    <div class="tile" role="img" aria-label="Shop owner at a counter" style="background:linear-gradient(135deg,#4a4038,#b8a99a)"></div>
  </div>
  <div class="size-panel" style="left:731px;top:596px;width:393px;height:249px;clip-path:polygon(0 0,100% 8%,100% 100%,0 92%);text-align:right">Square Videos that work best on FRIENDLANE (Square is 1080 X 1080)<small>Convert any video to this size for an additional fee of $39</small></div>

  <div class="size-panel" style="left:73px;top:1011px;width:392px;height:266px;clip-path:polygon(0 8%,100% 0,100% 100%,0 100%)">Vertical Videos that work best on STORIES for Friendlane, Photoloop and Blinkchat (1080 X 1920)<small>Convert any video to this size for an additional fee of $39</small></div>
  <div class="tiles" style="left:472px;top:962px">
    <div class="tile" role="img" aria-label="Portrait photo placeholder" style="background:linear-gradient(135deg,#7a6a58,#d8c4aa)"></div>
    <div class="tile" role="img" aria-label="Portrait photo placeholder" style="background:linear-gradient(135deg,#5c4a3c,#c9b39a)"></div>
    <div class="tile" role="img" aria-label="Portrait photo placeholder" style="background:linear-gradient(135deg,#3c3430,#b99d86)"></div>
    <div class="tile" role="img" aria-label="Athlete portrait placeholder" style="background:linear-gradient(135deg,#1d2740,#8e2a34)"></div>
  </div>
</section>

<footer class="footer">
  <div class="brand"><span class="brand-mark"></span><span class="brand-name">KESTREL</span></div>
  <div class="brand-tag">MARKETING VIDEOS MADE FOR YOU</div>
  <div class="footer-claim">CREATED BY A MARKETER FOR MARKETERS</div>
  <div class="footer-text">With Kestrel, you simply let us know what you want to promote and we will have your video ad finished as soon as 24 hours!</div>
  <h6 style="left:525px;top:58px">QUICK LINK</h6>
  <ul class="links"><li>How It Works</li><li>Term Of Service</li><li>Privacy Policy</li><li>Cookies Policy</li></ul>
  <h6 style="left:765px;top:58px">EMAIL SIGN UP</h6>
  <div class="email">Enter Email Address</div>
  <div class="signup">SIGN UP</div>
  <h6 style="left:765px;top:222px">FOLLOW US</h6>
  <div class="follow"><span></span><span></span><span></span><span></span><span></span><span></span></div>
</footer>
<div class="bottom">Copyright © 2019 Company Name . All Right Reserved<b>&#9650;</b></div>

</body>
</html>
```